Cash Balance Retirement Plan Services Page

We are looking to have a services/landing page created for one of our offerings. The goal of the page is to explain a relatively complex service (advanced retirement plan) by highlighting the benefits and uses for the plan such that it tells a story that encourages individuals and businesses that would benefit from the plans to reach out.

The page will be used both as a landing page (though secondarily) and as a page that many of our partners will show to their clients in order to generate interest. We help other people closes these deals so we want it to handle both.

Overall, we would want the page to incorporate the following sections/areas.
1. Headline and a place for a video at the top
2. Explanation of what a cash balance plan is (a paragraph or two)
3. These five benefits: These are the 7 we usually use, but only include five at a time so only need room for five.
a. Highest Tax Deductible Contributions Allowed
b. Significantly reduce your taxes
c. Potential Negative “Net Cost”
d. Owner & Executive Weighted Benefits
e. Retain and Attract Top Talen
f. Catch Up On decades of low retirement savings in a matter of years
g. Potential for life time income
4. A section comparing the contribution limits allowed for each plan type (Please see attached image as an example).
5. A place for a table of contribution amounts (This will just be an image. Also, attached).
6. A place for a compare table
6. Who should consider such a plan
7. Occasional banners for call to actions
8. FAQ

Our primary audience for this project are successful small business owners with a particular focus on medical professionals (doctors, chiropractors, dentists, plastic surgeons, etc.). In generally, they will be between 45 and 65 years old and earn $150k or more.

Because we work a lot with financial, business strategy, and insurance based products that require a significant investment by the client trust, professionalism, and sophistication are important attributes we wish to portray in the design of the page. Our preferred colors are blue or green. Though we are still working on figuring out the color scheme so your input as a designer is welcomed as your creativity can help us communicate the attributes we seek to embody for our clients.

In the attached document, I have included some additional information about the service itself if it helps to have some context, as well as a more flushed out outline of the details above.

Importantly, I am not a marketer so any creative input is always welcome if there is a best practice we are not incorporating in either our design requests or outline.

Here is the URL for our current page: https://www.brightvaleadvisors.com/physicianplan

Please don't let this page be your muse. We're trying to get away from it for a reason :) But it still will hopefully provide some helpful information, copy examples, and context.

Additionally, please don't feel like you need to read the full cash balance explanation. That's only if context will be helpful.

We are also going through a rebranding so please don't rely on the colors from the BrightValeAdvisors logo you may see on the website. I've attached two sample logos for the rebrand for context.

```html
<!DOCTYPE html>
<html lang="en">
<head>
<meta charset="utf-8">
<title>Cash Balance Plan | BrightVale</title>
<link href="https://fonts.googleapis.com/css2?family=Jost:wght@300;400;500;600;700&family=Arimo:wght@400;700&display=swap" rel="stylesheet">
<style>
:root{
  --teal:#2693bf;
  --navy:#0b3551;
  --ink:#222a30;
  --muted:#6b6f73;
  --soft:#f7f7f7;
  --white:#ffffff;
  --bar-ira:#a8e08a;
  --bar-401k:#10ad45;
  --bar-profit:#a4cdf5;
  --bar-cash:#1a78d8;
  --table-head:#1b2a9c;
}
*{box-sizing:border-box;margin:0;padding:0}
html,body{width:1200px;height:4119px;overflow:hidden}
body{position:relative;font-family:"Jost",sans-serif;color:var(--ink);background:var(--white)}
.section{position:absolute;left:0;width:1200px}
.abs{position:absolute}

/* hero */
.hero{top:0;height:685px;background:linear-gradient(180deg,#3f4a52 0%,#5c6770 45%,#3a444c 100%)}
.hero-bg{position:absolute;inset:0}
.hero-shade{position:absolute;inset:0;background:rgba(10,25,38,.35)}
.call{left:112px;top:38px;color:#fff;font-size:16px;font-weight:400;display:flex;align-items:center;gap:6px}
.brand{left:0;width:1200px;top:34px;text-align:center;color:#fff;font-weight:600;font-size:27px;letter-spacing:.5px}
.menu{left:1064px;top:40px}
.play{left:562px;top:221px}
.hero-title{left:200px;width:800px;top:312px;text-align:center;color:#fff;font-weight:600;font-size:40px;line-height:51px;white-space:nowrap}

/* what is */
.whatis{top:685px;height:294px;background:var(--soft)}
.whatis h2{position:absolute;left:112px;top:100px;color:var(--teal);font-weight:500;font-size:44px;line-height:53px}
.whatis p{position:absolute;left:600px;top:48px;width:490px;font-size:12.8px;line-height:25.8px;color:var(--muted);font-weight:300}

/* benefits */
.benefits{top:979px;height:941px;background:var(--white)}
.section-title{position:absolute;left:0;width:1200px;text-align:center;color:var(--teal);font-weight:500;font-size:42px}
.benefit{position:absolute;width:320px;text-align:center}
.benefit-icon{width:176px;height:176px;margin:0 auto;border-radius:50%;background:var(--navy);box-shadow:inset 0 0 0 8px var(--navy),inset 0 0 0 10px #fff}
.benefit h3{font-size:15.5px;font-weight:500;line-height:26px;margin-top:20px;color:var(--ink)}
.benefit p{width:300px;margin:12px auto 0;font-size:12px;line-height:23px;color:var(--muted);font-weight:300}

/* comparing */
.compare{top:1920px;height:493px;background:var(--white)}
.compare h2{position:absolute;left:112px;top:118px;color:var(--teal);font-weight:500;font-size:34px;line-height:45px}
.checklist{position:absolute;left:112px;top:226px;list-style:none}
.checklist li{font-size:19px;font-weight:300;line-height:49px;display:flex;align-items:center;gap:8px}
.rates{position:absolute;left:615px;top:55px;width:430px;height:300px;border:10px solid #2a2e33;border-radius:12px 12px 4px 4px;background:var(--white)}
.rates table{width:100%;border-collapse:collapse;font-family:"Arimo",sans-serif;font-size:9.5px}
.rates th{background:var(--table-head);color:#fff;text-align:left;font-weight:700;padding:4px 4px;vertical-align:top;line-height:12px}
.rates td{padding:3px 4px;color:#111;border-bottom:1px solid #d0d6e8}
.rates tr:nth-child(even) td{background:#e6eaf6}
.rates td.strong{font-weight:700}
.rates .rates-brand{text-align:center;font-weight:600;font-size:27px;color:var(--navy);margin-top:30px}

/* chart */
.chart-card{top:2413px;left:112px;width:976px;height:448px;background:var(--white);box-shadow:0 0 14px rgba(0,0,0,.12)}
.chart-card .lbl{position:absolute;font-family:"Arimo",sans-serif;font-weight:700;font-size:18px;line-height:21px;text-align:center;color:#111}
.chart-card .bar{position:absolute;width:66px}
.chart-card .note{position:absolute;left:760px;top:114px;width:100px;font-family:"Arimo",sans-serif;font-size:15.5px;line-height:18px;text-align:center;color:#111}

/* who */
.who{top:2861px;height:675px;background:var(--white)}
.who h2{position:absolute;left:112px;top:86px;color:var(--teal);font-weight:500;font-size:42px;line-height:50px}
.who ul{position:absolute;left:112px;top:212px;width:460px;list-style:none}
.who li{position:relative;padding-left:22px;font-size:11.5px;line-height:34.5px;font-weight:300;color:#333}
.who li svg{position:absolute;left:0;top:11px}
.btn{position:absolute;background:var(--navy);color:#fff;font-weight:600;font-size:15px;display:flex;align-items:center;justify-content:center}
.portrait{position:absolute;left:635px;top:96px;width:451px;height:531px;background:linear-gradient(160deg,#c9d4da 0%,#e8ecee 50%,#aebcc4 100%)}

/* faq */
.faq{top:3536px;height:499px;background:var(--white)}
.faq-item{position:absolute;left:240px;width:720px;height:48px;border:1px solid #dcdcdc;background:#fff;display:flex;align-items:center;justify-content:space-between;padding:0 14px;font-size:14px;font-weight:300;color:#444}

/* footer */
.footer{top:4035px;height:84px;background:var(--teal);color:#fff;text-align:center;font-size:15px;font-weight:500;line-height:84px}
</style>
</head>
<body>

<header class="section hero">
  <div class="hero-bg" role="img" aria-label="Photograph of a team of doctors walking through a bright hospital corridor"></div>
  <div class="hero-shade"></div>
  <div class="abs call">
    <svg width="14" height="14" viewBox="0 0 24 24"><path fill="#2aa6d6" d="M6.6 10.8a15.1 15.1 0 0 0 6.6 6.6l2.2-2.2c.3-.3.7-.4 1-.2 1.1.4 2.3.6 3.6.6.6 0 1 .4 1 1V20c0 .6-.4 1-1 1A17 17 0 0 1 3 4c0-.6.4-1 1-1h3.5c.6 0 1 .4 1 1 0 1.3.2 2.5.6 3.6.1.3 0 .7-.2 1z"/></svg>
    Call Now - +1 555 010 2040
  </div>
  <div class="abs brand">BRIGHTVALE</div>
  <svg class="abs menu" width="24" height="18" viewBox="0 0 24 18"><path d="M0 1h24M4 9h20M0 17h24" stroke="#fff" stroke-width="2"/></svg>
  <svg class="abs play" width="76" height="76" viewBox="0 0 76 76"><circle cx="38" cy="38" r="35" fill="none" stroke="#2aa6d6" stroke-width="3"/><path d="M30 24 L52 38 L30 52 Z" fill="none" stroke="#2aa6d6" stroke-width="3" stroke-linejoin="round"/></svg>
  <h1 class="abs hero-title">Are you healthy enough that<br>you are at risk of outliving your<br>retirement savings?</h1>
</header>

<section class="section whatis">
  <h2>What is a Cash-<br>Balance Plan</h2>
  <p>A cash balance plan is a retirement plan specifically for small business owners, doctors, lawyers, and other high-income professionals. It allows for the highest tax-deductible contribution limits in the market, and the older you get, the higher those limits go. You then get an option for guaranteed income for life or a one time, lump payout. They are a hybrid plan that combines a the benefits of a defined benefit plan (Pensions) with those of a defined contribution plan (IRA, 401k, etc.). They are often not dependent on the stock market, which is a huge boon.</p>
</section>

<section class="section benefits">
  <h2 class="section-title" style="top:62px">Benefits</h2>

  <div class="benefit" style="left:102px;top:149px">
    <div class="benefit-icon" role="img" aria-label="Icon illustration of a tax form with a check mark"></div>
    <h3>Highest Tax Deductible<br>Contributions Allowed</h3>
    <p>Most retirement plans in the US (IRAs, 401(k), SEP) allow $7k, $27k, or $61k a year to be contributed to retirement plans. This is a major disadvantage to individuals who have a significant income. These plans go as high as $417k.</p>
  </div>

  <div class="benefit" style="left:442px;top:149px">
    <div class="benefit-icon" role="img" aria-label="Icon illustration of coin stacks and a percent sign"></div>
    <h3>Significantly reduce your<br>taxes</h3>
    <p>Because these plans are tax-advantaged, the contributions are 100% tax deductible. That means an individual who contributes the full $417k annually will reduce their taxes by as much as $100k a year.</p>
  </div>

  <div class="benefit" style="left:779px;top:149px">
    <div class="benefit-icon" role="img" aria-label="Icon illustration of a calculator with a dollar coin"></div>
    <h3>Potential Negative<br>“Net Cost”</h3>
    <p>Many businesses are unable to contribute to their own retirement because they also have to pay for employees. Even if they want to, the cost is often prohibitive. These plans can be designed</p>
  </div>

  <div class="benefit" style="left:267px;top:552px">
    <div class="benefit-icon" role="img" aria-label="Icon illustration of an executive in a suit"></div>
    <h3>Owner &amp; Executive Weighted<br>Benefits</h3>
    <p>hese plans allow greater contribution for owners and executives who are older with high income.</p>
  </div>

  <div class="benefit" style="left:606px;top:552px">
    <div class="benefit-icon" role="img" aria-label="Icon illustration of hands holding a star"></div>
    <h3>Retain and Attract Top<br>Talent</h3>
    <p>e.These plans—on top of all the benefits provided the business owners or doctors—are great for employees. Offering them helps retain and attract top talent.</p>
  </div>
</section>

<section class="section compare">
  <h2>Comparing the contribution<br>limits allowed</h2>
  <ul class="checklist">
    <li><svg width="14" height="14" viewBox="0 0 14 14"><circle cx="7" cy="7" r="7" fill="var(--teal)"/><path d="M4 7l2 2 4-4" stroke="#fff" stroke-width="1.8" fill="none"/></svg>Allowable Tax-Deductible Contribution by Age</li>
    <li><svg width="14" height="14" viewBox="0 0 14 14"><circle cx="7" cy="7" r="7" fill="var(--teal)"/><path d="M4 7l2 2 4-4" stroke="#fff" stroke-width="1.8" fill="none"/></svg>How much is your estimated tax savings?</li>
  </ul>
  <div class="rates">
    <table>
      <thead><tr><th>Starting Plan at Age:</th><th>Max Monthly Retirement Benefit:</th><th>Lump Sum at Retirement:</th><th>Illustrative Contribution Limits:</th><th>Estimated Tax Savings:</th><th>“Net Cost” after Tax Savings:</th></tr></thead>
      <tbody>
        <tr><td>40</td><td>$20,417</td><td>$2,959,124</td><td class="strong">$141,358</td><td>$56,543</td><td>$84,814</td></tr>
        <tr><td>45</td><td>$20,417</td><td>$2,959,124</td><td class="strong">$178,753</td><td>$71,501</td><td>$107,252</td></tr>
        <tr><td>50</td><td>$20,417</td><td>$2,959,124</td><td class="strong">$246,962</td><td>$98,784</td><td>$148,177</td></tr>
        <tr><td>55</td><td>$20,417</td><td>$2,959,124</td><td class="strong">$382,181</td><td>$152,872</td><td>$229,308</td></tr>
        <tr><td>60</td><td>$10,208</td><td>$1,479,561</td><td class="strong">$400,418</td><td>$160,192</td><td>$240,225</td></tr>
      </tbody>
    </table>
    <div class="rates-brand">BRIGHTVALE</div>
  </div>
</section>

<section class="section chart-card">
  <div class="lbl" style="left:92px;top:255px;width:100px">Annual Contributions Limits</div>
  <div class="lbl" style="left:210px;top:262px;width:92px">$6,000<br>($7000)</div>
  <div class="bar" style="left:222px;top:309px;height:14px;background:var(--bar-ira)"></div>
  <div class="lbl" style="left:222px;top:344px;width:66px">IRA</div>
  <div class="lbl" style="left:353px;top:240px;width:100px">$20,500<br>($27,000)</div>
  <div class="bar" style="left:370px;top:286px;height:37px;background:var(--bar-401k)"></div>
  <div class="lbl" style="left:360px;top:344px;width:86px">401(k)</div>
  <div class="lbl" style="left:500px;top:210px;width:100px">$61,000</div>
  <div class="bar" style="left:517px;top:233px;height:90px;background:var(--bar-profit)"></div>
  <div class="lbl" style="left:514px;top:344px;width:66px">Profit<br>Sharin<br>g</div>
  <div class="lbl" style="left:647px;top:60px;width:100px">$416,000</div>
  <div class="bar" style="left:664px;top:83px;height:240px;background:var(--bar-cash)"></div>
  <div class="lbl" style="left:652px;top:344px;width:90px">Cash<br>Balance<br>Plan</div>
  <div class="note">*Your contribution limits will be based on age and salary and may not reach the max contribution amount.</div>
</section>

<section class="section who">
  <h2>Who should consider<br>such a plan</h2>
  <ul>
    <li><svg width="12" height="12" viewBox="0 0 14 14"><circle cx="7" cy="7" r="7" fill="var(--navy)"/><path d="M4 7l2 2 4-4" stroke="#fff" stroke-width="1.8" fill="none"/></svg>You are looking to maximize your tax deductions.</li>
    <li><svg width="12" height="12" viewBox="0 0 14 14"><circle cx="7" cy="7" r="7" fill="var(--navy)"/><path d="M4 7l2 2 4-4" stroke="#fff" stroke-width="1.8" fill="none"/></svg>Your income pushes you beyond the contribution limits of the lower retirement plans such as 401(k)s, SEPs or profit sharing plans.</li>
    <li><svg width="12" height="12" viewBox="0 0 14 14"><circle cx="7" cy="7" r="7" fill="var(--navy)"/><path d="M4 7l2 2 4-4" stroke="#fff" stroke-width="1.8" fill="none"/></svg>You are in your 40s, 50s, or 60s and don’t want the “2nd best” plan.</li>
    <li><svg width="12" height="12" viewBox="0 0 14 14"><circle cx="7" cy="7" r="7" fill="var(--navy)"/><path d="M4 7l2 2 4-4" stroke="#fff" stroke-width="1.8" fill="none"/></svg>You want an option to GUARANTEE a retirement benefit.</li>
    <li><svg width="12" height="12" viewBox="0 0 14 14"><circle cx="7" cy="7" r="7" fill="var(--navy)"/><path d="M4 7l2 2 4-4" stroke="#fff" stroke-width="1.8" fill="none"/></svg>You are looking for a way to “catch-up” on retirement savings that provides massive tax savings.</li>
  </ul>
  <div class="btn" style="left:112px;top:461px;width:195px;height:51px">Read More</div>
  <div class="portrait" role="img" aria-label="Photograph of a smiling female doctor in a white coat"></div>
</section>

<section class="section faq">
  <h2 class="section-title" style="top:30px">FAQ</h2>
  <div class="faq-item" style="top:99px">What is your company name?<svg width="14" height="14" viewBox="0 0 14 14"><circle cx="7" cy="7" r="6" fill="none" stroke="#333" stroke-width="1.6"/><path d="M7 4v6M4 7h6" stroke="#333" stroke-width="1.6"/></svg></div>
  <div class="faq-item" style="top:155px">Please provide your website link.<svg width="14" height="14" viewBox="0 0 14 14"><circle cx="7" cy="7" r="6" fill="none" stroke="#333" stroke-width="1.6"/><path d="M7 4v6M4 7h6" stroke="#333" stroke-width="1.6"/></svg></div>
  <div class="faq-item" style="top:211px">Where is your company based / what areas do you operate in?<svg width="14" height="14" viewBox="0 0 14 14"><circle cx="7" cy="7" r="6" fill="none" stroke="#333" stroke-width="1.6"/><path d="M7 4v6M4 7h6" stroke="#333" stroke-width="1.6"/></svg></div>
  <div class="faq-item" style="top:267px">What is your company slogan or mission statement?<svg width="14" height="14" viewBox="0 0 14 14"><circle cx="7" cy="7" r="6" fill="none" stroke="#333" stroke-width="1.6"/><path d="M7 4v6M4 7h6" stroke="#333" stroke-width="1.6"/></svg></div>
  <div class="faq-item" style="top:323px">How would you describe your business in one sentence? What is the basic function of<svg width="14" height="14" viewBox="0 0 14 14"><circle cx="7" cy="7" r="6" fill="none" stroke="#333" stroke-width="1.6"/><path d="M7 4v6M4 7h6" stroke="#333" stroke-width="1.6"/></svg></div>
  <div class="btn" style="left:502px;top:403px;width:196px;height:51px">View More</div>
</section>

<footer class="section footer">© 2022 All Rights Reserved</footer>

</body>
</html>
```